Sophisticated, clean website reflecting my feminine, playful side to sell my abstract art,

I need a website no more than 3 pages to showcase my paintings, a little about me and some contact info. I do abstracts so looking for something a little edgy, yet feminine and current.
Updates

Hi there, These are some artists websites that I Iike: Marnelvoss.com (I like how airy it is) peterwallombry.com garethpolvens.com (I like how it scrolls) I'll need a place for a photo ( a headshot-i do not have it yet so I'll need to be able to upload that later) as well as an area for my bio. Also, it's important that I will be able to upload any new photos and descriptions easily so it should be user friendly. Lastly, I like in a sunny place so would like to have this seem upbeat and playful as that is how i like to paint. thanks-I'm trying to upload my photos now -

Target Market(s)

ppl ages 35-70 who want large scale art for their homes

Industry/Entity Type

art

Coding

Coded - Design and coding required

Number of Pages Required

3 page

Colors

Designer to choose colors to be used in the design.

Requirements
Must have
• photos of my art, a place for my bio, be easy to reach me. tasteful-nothing too "in your face" -my clients are pretty high end and organized. They like clean lines
Nice to have
• sophisticated background, muted tones in the back-similar clean font throughout-no cursive
Should not have
• too many dark areas. Too many blocks of color. Too serious.

```html
<!DOCTYPE html>
<html lang="en">
<head>
<meta charset="utf-8">
<title>Hollis Wren Art</title>
<link rel="stylesheet" href="https://fonts.googleapis.com/css2?family=Lato:wght@400;700&family=Poppins:wght@500;600;700&family=Permanent+Marker&family=Roboto:wght@400&display=swap">
<style>
:root{
  --pink:#f54ea4;
  --blue:#1583e8;
  --ink:#141414;
  --text:#2b2b2b;
  --muted:#6d6d6d;
  --paper:#ffffff;
  --mist:#e7e7e9;
  --black:#000000;
  --frame:#c48a45;
}
*{box-sizing:border-box;margin:0;padding:0}
html,body{width:1200px;height:2837px;overflow:hidden}
body{position:relative;background:var(--paper);font-family:"Lato",sans-serif;color:var(--text)}
.abs{position:absolute}

/* hero */
.hero-bg{left:0;top:0;width:1200px;height:643px;
  background:linear-gradient(135deg,#6e6548 0%,#5d686b 45%,#55636b 75%,#6f7068 100%)}
.hero-edge{left:0;top:520px}
.nav{left:111px;top:41px;width:977px;height:68px;background:var(--paper);border-radius:4px;display:flex;align-items:center;padding:0 22px 0 32px}
.brand{font-family:"Poppins",sans-serif;font-weight:700;font-size:24px;color:var(--ink);width:350px;white-space:nowrap}
.nav-links{display:flex;gap:55px;font-size:15px;color:var(--ink)}
.nav-links .active{color:var(--blue);border-bottom:2px solid var(--blue);padding-bottom:2px}
.btn{display:inline-flex;align-items:center;justify-content:center;border-radius:22px;font-family:"Poppins",sans-serif;font-weight:600;font-size:15px;color:#fff;text-transform:uppercase}
.btn-pink{background:var(--pink)}
.btn-blue{background:var(--blue)}
.login{margin-left:auto;width:97px;height:42px}
.welcome{left:111px;top:193px;font-size:35px;line-height:42px;color:#fff;letter-spacing:.5px}
.hero-title{left:111px;top:240px;font-family:"Permanent Marker",sans-serif;font-weight:400;font-size:60px;line-height:72px;color:var(--pink);letter-spacing:2px;white-space:nowrap}
.hero-copy{left:111px;top:386px;width:490px;font-size:15px;line-height:26px;color:#fff}
.get-started{left:111px;top:452px;width:138px;height:42px}
.hero-art{left:705px;top:143px;width:266px;height:377px;border:10px solid var(--frame);background:linear-gradient(160deg,#dde1e5,#cfd3d6)}

/* about */
.about-frame{left:111px;top:741px;width:489px;height:367px;background:#fff;border-radius:20px;box-shadow:0 2px 10px rgba(0,0,0,.2);padding:9px 10px}
.about-art{width:100%;height:100%;border-radius:16px;background:linear-gradient(135deg,#b9cfbb,#8fb496)}
.section-title{font-family:"Permanent Marker",sans-serif;font-weight:400;font-size:32px;line-height:40px;color:var(--ink);letter-spacing:1px}
.section-title span{color:var(--pink)}
.about-title{left:666px;top:730px}
.about-copy{left:666px;top:791px;width:425px;font-size:15.5px;line-height:25.7px;color:var(--text)}
.learn-more{left:667px;top:1023px;width:138px;height:42px}

/* paintings */
.paint-bg{left:0;top:1193px;width:1200px;height:617px;background:linear-gradient(135deg,#ececee,#e2e2e5)}
.paint-title{left:0;top:1270px;width:1200px;text-align:center}
.card{top:1347px;width:236px;height:375px;background:#fff;padding:17px}
.card-top{display:flex;justify-content:space-between;align-items:center;height:18px}
.avatar{width:24px;height:24px;border-radius:50%;background:#7f8b8a}
.dots{display:flex;gap:5px}
.dots i{width:5px;height:5px;border-radius:50%;background:#555;display:block}
.card-art{margin-top:16px;height:187px;background:linear-gradient(135deg,#e3e0d8,#cdd1d5)}
.card-head{display:flex;align-items:center;margin-top:12px;white-space:nowrap}
.card-name{font-family:"Roboto",sans-serif;font-size:21px;color:var(--ink)}
.tag{margin-left:10px;font-size:12px;color:var(--pink);display:flex;align-items:center;gap:5px}
.card-copy{margin-top:18px;font-family:"Roboto",sans-serif;font-size:15.5px;line-height:22px;color:var(--ink)}

/* contact */
.contact-bg{left:0;top:2150px;width:1200px;height:300px;background:linear-gradient(180deg,#fff 0%,#eceef0 50%,#d9dee0 100%)}
.contact-title{left:0;top:1888px;width:1200px;text-align:center}
.field{background:#fff;box-shadow:0 2px 8px rgba(0,0,0,.12);border-radius:3px;font-size:15px;color:var(--muted);padding:0 26px;display:flex;align-items:center}
.field.msg{align-items:flex-start;padding-top:20px}
.submit{left:532px;top:2257px;width:136px;height:42px}

/* footer */
.footer-bg{left:0;top:2420px;width:1200px;height:417px;background:var(--black)}
.footer-edge{left:0;top:2270px}
.foot-brand{left:111px;top:2492px;font-family:"Poppins",sans-serif;font-weight:700;font-size:35px;line-height:52px;color:#fff}
.socials{left:111px;top:2615px;display:flex;gap:5px}
.socials i{display:block;width:22px;height:22px;border:1.5px solid #fff;border-radius:50%}
.foot-head{font-family:"Poppins",sans-serif;font-weight:700;font-size:22px;color:#fff}
.foot-list{font-size:15.5px;line-height:25.5px;color:#fff;list-style:none}
.contact-item{display:flex;gap:18px;align-items:center;color:#fff;font-size:15.5px;line-height:25.5px}
.contact-item b{font-weight:700;display:block}
.icon{width:44px;height:44px;border-radius:50%;background:var(--pink);display:flex;align-items:center;justify-content:center;flex:none}
.divider{left:111px;top:2756px;width:977px;height:1px;background:#2e2e2e}
.copy{left:0;top:2778px;width:1200px;text-align:center;color:#fff;font-size:15.5px}
</style>
</head>
<body>

<div class="abs hero-bg" role="img" aria-label="Muted abstract painting backdrop in ochre and slate tones"></div>
<svg class="abs hero-edge" width="1200" height="125" viewBox="0 0 1200 125" aria-hidden="true">
  <path fill="#ffffff" d="M0 80 L40 70 L90 85 L150 60 L210 78 L260 58 L330 74 L400 50 L470 68 L540 45 L610 62 L680 40 L760 55 L840 30 L920 48 L1000 22 L1080 38 L1140 15 L1200 28 L1200 125 L1100 125 L1050 110 L980 123 L900 100 L820 118 L740 95 L660 120 L580 104 L500 122 L420 100 L340 118 L260 98 L190 125 L110 108 L60 125 L0 125 Z"/>
</svg>

<nav class="abs nav">
  <div class="brand">Hollis Wren Art</div>
  <div class="nav-links">
    <span class="active">Home</span><span>About Me</span><span>Paintings</span><span>Contact Us</span>
  </div>
  <a class="btn btn-pink login">Log in</a>
</nav>

<div class="abs welcome">WELCOME TO</div>
<h1 class="abs hero-title">HOLLIS<br>WREN ART</h1>
<p class="abs hero-copy">Art reflecting the game we call life- joyous, sometimes w/ an edge but always going in with a curious mind and an open heart. dm for inquiries</p>
<a class="abs btn btn-blue get-started">Get started</a>
<div class="abs hero-art" role="img" aria-label="Framed abstract painting"></div>

<section>
  <div class="abs about-frame"><div class="about-art" role="img" aria-label="Abstract painting in greens"></div></div>
  <h2 class="abs section-title about-title">ABOUT <span>ME</span></h2>
  <p class="abs about-copy">Lorem ipsum dolor sit amet, consectetur adipiscing elit, sed do eiusmod tempor incididunt ut labore et dolore magna aliqua. Ut enim ad minim veniam, quis nostrud exercitation ullamco laboris nisi ut aliquip ex ea commodo consequat. Duis aute irure dolor in reprehenderit in voluptate velit esse cillum dolore eu fugiat nulla pariatur. Excepteur sint occaecat cupidatat non proident, sunt in culpa qui officia deserunt mollit anim id est laborum.</p>
  <a class="abs btn btn-pink learn-more">Learn more</a>
</section>

<section>
  <div class="abs paint-bg" role="img" aria-label="Soft grey watercolour wash background"></div>
  <h2 class="abs section-title paint-title">MY <span>PAINTINGS</span></h2>

  <article class="abs card" style="left:111px">
    <div class="card-top"><span class="avatar"></span><span class="dots"><i></i><i></i><i></i></span></div>
    <div class="card-art" role="img" aria-label="Abstract painting"></div>
    <div class="card-head"><span class="card-name">Lorem ipsum</span><span class="tag"><svg width="16" height="16" viewBox="0 0 16 16"><path fill="#f54ea4" d="M8 1h7v7l-7 7-7-7z"/><circle cx="12" cy="4" r="1.3" fill="#fff"/></svg>Painting</span></div>
    <p class="card-copy">Lorem ipsum dolor sit amet, consectetur adipiscing elit</p>
  </article>

  <article class="abs card" style="left:358px">
    <div class="card-top"><span class="avatar"></span><span class="dots"><i></i><i></i><i></i></span></div>
    <div class="card-art" role="img" aria-label="Abstract painting"></div>
    <div class="card-head"><span class="card-name">Lorem ipsum</span><span class="tag"><svg width="16" height="16" viewBox="0 0 16 16"><path fill="#f54ea4" d="M8 1h7v7l-7 7-7-7z"/><circle cx="12" cy="4" r="1.3" fill="#fff"/></svg>Painting</span></div>
    <p class="card-copy">Lorem ipsum dolor sit amet, consectetur adipiscing elit</p>
  </article>

  <article class="abs card" style="left:604px">
    <div class="card-top"><span class="avatar"></span><span class="dots"><i></i><i></i><i></i></span></div>
    <div class="card-art" role="img" aria-label="Abstract painting"></div>
    <div class="card-head"><span class="card-name">Lorem ipsum</span><span class="tag"><svg width="16" height="16" viewBox="0 0 16 16"><path fill="#f54ea4" d="M8 1h7v7l-7 7-7-7z"/><circle cx="12" cy="4" r="1.3" fill="#fff"/></svg>Painting</span></div>
    <p class="card-copy">Lorem ipsum dolor sit amet, consectetur adipiscing elit</p>
  </article>

  <article class="abs card" style="left:851px">
    <div class="card-top"><span class="avatar"></span><span class="dots"><i></i><i></i><i></i></span></div>
    <div class="card-art" role="img" aria-label="Abstract painting"></div>
    <div class="card-head"><span class="card-name">Lorem ipsum</span><span class="tag"><svg width="16" height="16" viewBox="0 0 16 16"><path fill="#f54ea4" d="M8 1h7v7l-7 7-7-7z"/><circle cx="12" cy="4" r="1.3" fill="#fff"/></svg>Painting</span></div>
    <p class="card-copy">Lorem ipsum dolor sit amet, consectetur adipiscing elit</p>
  </article>
</section>

<section>
  <div class="abs contact-bg" role="img" aria-label="Pale watercolour texture"></div>
  <h2 class="abs section-title contact-title">CONTACT <span>US</span></h2>
  <div class="abs field" style="left:268px;top:1969px;width:322px;height:61px">First Name</div>
  <div class="abs field" style="left:609px;top:1969px;width:322px;height:61px">Last Name</div>
  <div class="abs field" style="left:268px;top:2048px;width:322px;height:62px">Email</div>
  <div class="abs field" style="left:609px;top:2048px;width:322px;height:62px">Phone</div>
  <div class="abs field msg" style="left:268px;top:2127px;width:663px;height:106px">Message</div>
  <a class="abs btn btn-pink submit">Submit</a>
</section>

<footer>
  <div class="abs footer-bg"></div>
  <svg class="abs footer-edge" width="1200" height="152" viewBox="0 0 1200 152" aria-hidden="true">
    <path fill="#000" d="M0 50 L60 62 L120 40 L200 70 L270 48 L350 75 L420 52 L500 80 L580 58 L660 85 L740 60 L820 88 L900 55 L980 70 L1060 35 L1130 48 L1200 20 L1200 152 L0 152 Z"/>
  </svg>

  <div class="abs foot-brand">Hollis<br>Wren Art</div>
  <div class="abs socials"><i></i><i></i><i></i></div>

  <div class="abs" style="left:430px;top:2472px">
    <div class="foot-head">Contact us</div>
    <div class="contact-item" style="margin-top:24px">
      <span class="icon"><svg width="16" height="20" viewBox="0 0 16 20"><path fill="#fff" d="M8 0a7 7 0 0 0-7 7c0 5 7 13 7 13s7-8 7-13a7 7 0 0 0-7-7zm0 10a3 3 0 1 1 0-6 3 3 0 0 1 0 6z"/></svg></span>
      <span>Lorem ipsum dolor sit amet,<br>consectetur adipiscing</span>
    </div>
    <div class="contact-item" style="margin-top:20px">
      <span class="icon"><svg width="18" height="18" viewBox="0 0 18 18"><path fill="#fff" d="M4 1l3 4-2 2c1 2 3 4 5 5l2-2 4 3-2 3C8 16 2 10 1 3z"/></svg></span>
      <span><b>Call Us</b>+1 888 888 8888</span>
    </div>
    <div class="contact-item" style="margin-top:20px">
      <span class="icon"><svg width="18" height="14" viewBox="0 0 18 14"><rect width="18" height="14" rx="2" fill="#fff"/><path d="M1 2l8 6 8-6" stroke="#f54ea4" stroke-width="1.6" fill="none"/></svg></span>
      <span><b>Email Us</b>info@holliswrenart.com</span>
    </div>
  </div>

  <div class="abs" style="left:766px;top:2472px">
    <div class="foot-head">Menu</div>
    <ul class="foot-list" style="margin-top:20px"><li>Home</li><li>About Me</li><li>Paintings</li><li>Contact us</li></ul>
  </div>

  <div class="abs" style="left:942px;top:2472px">
    <div class="foot-head">Other Links</div>
    <ul class="foot-list" style="margin-top:20px"><li>Terms &amp; Conditions</li><li>Privacy Policy</li><li>About Us</li><li>Support</li></ul>
  </div>

  <div class="abs divider"></div>
  <p class="abs copy">©Copyrights 2022 Hollis Wren Art &nbsp; | &nbsp; All Rights Reserved</p>
</footer>

</body>
</html>
```